Family business needs stationery redesign with new logo

Family owned company, established in 1987 wanting a brand 'refresh'. We are an electrical, refrigeration and construction company based in the Barkly Region Northern Territory, Australia. We have a new logo we would like to use which is uploaded along with our current letterhead and email signature. We are also dropping the word 'contractors' so please do not include this on any designs. Please note also, the 'orange' color used in our logo and designs should be Northern Territory red ochre which is as follows:

RGB (Hex): #C75B12
PantoneĀ® 159 C
CMYK: 1 / 74 / 100 / 7

We are needing our stationery redesigned using our new logo. Please include letterheads, business cards, envelopes, and email signatures.

We currently use our business letterheads for quotations, invoices, letters, HR matters, and internal memos.

We also need a separate simplified letterhead for internal paperwork such as employee leave forms, meeting agendas, and meeting minutes etc.

Reason: Needing more submissions of full package designs. We are wanting all our stationery, including business cards, letterheads, email signatures, envelopes, etc to be cohesive. We also require ALL the information, as supplied on our template letterhead, to be included on the new letterhead designs. including electrical license no.etc Thank you, R&W

Reason: needing more time as work has got in the way of looking over designs. A lot of designs not meeting the brief/criteria.

Industry/Entity Type

Business

Colors
0355a3
f37122

Requirements
Must have
• The 'orange' color used in the designs should be Northern Territory red ochre which is as follows:
• RGB (Hex): #C75B12
• PantoneĀ® 159 C
• CMYK: 1 / 74 / 100 / 7
• ***MUST INCLUDE ALL INFORMATION THAT IS ON OUR CURRENT LETTERHEAD***
Should not have
• Please do not include the word 'contractors'

```html
<!DOCTYPE html>
<html lang="en">
<head>
<meta charset="utf-8">
<title>R&amp;W Stationery Set</title>
<link rel="stylesheet" href="https://fonts.googleapis.com/css2?family=Tinos:wght@400;700&display=swap">
<style>
  :root {
    --navy: #23346e;
    --ochre: #c75b12;
    --paper: #ffffff;
    --ground: #eceef2;
    --flap-shadow: #d3d5d9;
    --serif: "Tinos", "Times New Roman", serif;
  }
  * { box-sizing: border-box; margin: 0; padding: 0; }
  html, body { width: 1200px; height: 1200px; overflow: hidden; }
  body { background: var(--ground); font-family: var(--serif); position: relative; }

  .icon { width: 1em; height: 1em; fill: currentColor; flex: none; }

  .brand { display: inline-flex; align-items: center; gap: .3em; font-weight: 700; line-height: 1; }
  .brand-dot { width: .32em; height: .32em; border-radius: 50%; background: var(--ochre); }

  /* Letterhead */
  .letterhead {
    position: absolute; left: 40px; top: 60px; width: 540px; height: 764px;
    background: var(--paper); box-shadow: 0 2px 10px rgba(0,0,0,.12);
  }
  .letterhead-header { position: absolute; left: 40px; right: 40px; top: 44px; height: 80px; border-bottom: 3px solid var(--navy); display: flex; justify-content: space-between; align-items: flex-start; }
  .letterhead-header .brand { font-size: 46px; color: var(--navy); margin-top: 8px; }
  .letterhead-address { color: var(--ochre); font-weight: 700; font-size: 11.5px; letter-spacing: .04em; text-align: right; line-height: 1.7; text-transform: uppercase; }
  .letterhead-footer { position: absolute; left: 40px; right: 40px; bottom: 36px; border-top: 3px solid var(--ochre); padding-top: 12px; display: flex; justify-content: space-between; font-size: 12px; font-weight: 700; color: var(--navy); }
  .footer-item { display: flex; align-items: center; gap: 6px; }
  .footer-item .icon { color: var(--ochre); font-size: 12px; }

  /* Envelope front */
  .envelope-front {
    position: absolute; left: 620px; top: 60px; width: 540px; height: 270px;
    background: var(--navy); color: var(--paper); box-shadow: 0 2px 10px rgba(0,0,0,.15);
  }
  .envelope-return { position: absolute; left: 36px; top: 34px; font-size: 15px; font-weight: 700; letter-spacing: .03em; line-height: 1.5; }
  .envelope-row { display: flex; gap: 12px; align-items: flex-start; margin-bottom: 8px; }
  .envelope-row .icon { color: var(--ochre); font-size: 18px; margin-top: 2px; }
  .envelope-front .brand { position: absolute; right: 34px; bottom: 28px; font-size: 58px; color: var(--paper); }

  /* Envelope back */
  .envelope-back {
    position: absolute; left: 620px; top: 360px; width: 540px; height: 270px;
    background: var(--paper); box-shadow: 0 2px 10px rgba(0,0,0,.12); overflow: hidden;
  }
  .envelope-back svg { position: absolute; inset: 0; }

  /* Business cards */
  .card { position: absolute; width: 250px; height: 150px; border-radius: 12px; overflow: hidden; box-shadow: 0 2px 10px rgba(0,0,0,.15); }
  .card-front { left: 620px; top: 670px; background: var(--paper); }
  .card-front .brand { position: absolute; right: 20px; top: 18px; font-size: 30px; color: var(--navy); }
  .card-name-band { position: absolute; left: 0; bottom: 0; width: 110px; height: 86px; background: var(--ochre); color: var(--paper); padding: 18px 10px 0 14px; }
  .card-name { font-size: 15px; letter-spacing: .05em; }
  .card-title { font-size: 6.5px; text-transform: uppercase; letter-spacing: .05em; margin-top: 4px; line-height: 1.3; }
  .card-contact-band { position: absolute; right: 0; bottom: 0; width: 140px; height: 86px; background: var(--navy); color: var(--paper); padding: 10px 8px 0 12px; font-size: 7px; font-weight: 700; line-height: 1.25; }
  .card-contact-row { display: flex; gap: 5px; margin-bottom: 3px; }
  .card-contact-row .icon { color: var(--ochre); font-size: 8px; }
  .card-notch { position: absolute; left: 40px; top: 58px; width: 0; height: 0; border-left: 7px solid transparent; border-right: 7px solid transparent; border-top: 7px solid var(--paper); }

  .card-back { left: 890px; top: 670px; background: var(--ochre); }
  .card-back .brand { position: absolute; left: 0; right: 0; top: 40px; justify-content: center; font-size: 48px; color: var(--paper); }
  .card-back .brand-dot { background: var(--navy); }
  .card-back-strip { position: absolute; left: 0; right: 0; bottom: 0; height: 26px; background: var(--navy); color: var(--paper); display: flex; align-items: center; justify-content: center; gap: 6px; font-size: 8px; font-weight: 700; }
  .card-back-strip .icon { color: var(--ochre); font-size: 10px; }
  .card-back-strip::before { content: ""; position: absolute; top: -1px; left: 50%; margin-left: -5px; border-left: 5px solid transparent; border-right: 5px solid transparent; border-top: 5px solid var(--ochre); }
</style>
</head>
<body>

<svg width="0" height="0" style="position:absolute" aria-hidden="true">
  <defs>
    <symbol id="i-pin" viewBox="0 0 24 24"><path d="M12 2a7 7 0 0 0-7 7c0 5 7 13 7 13s7-8 7-13a7 7 0 0 0-7-7zm0 9.5A2.5 2.5 0 1 1 12 6.5a2.5 2.5 0 0 1 0 5z"/></symbol>
    <symbol id="i-phone" viewBox="0 0 24 24"><path d="M3 9c0-3 4-5 9-5s9 2 9 5v1h-5V8H8v2H3zM6 11h12l2 8H4zm6 2a2.5 2.5 0 1 0 0 5 2.5 2.5 0 0 0 0-5z"/></symbol>
    <symbol id="i-mobile" viewBox="0 0 24 24"><path d="M7 2h10a1 1 0 0 1 1 1v18a1 1 0 0 1-1 1H7a1 1 0 0 1-1-1V3a1 1 0 0 1 1-1zm1 3v13h8V5zm4 14.5a1 1 0 1 0 0 .1z"/></symbol>
    <symbol id="i-mail" viewBox="0 0 24 24"><path d="M2 5h20v14H2zm2 2v.5l8 5 8-5V7zm0 3v7h16v-7l-8 5z"/></symbol>
    <symbol id="i-globe" viewBox="0 0 24 24"><path d="M12 2a10 10 0 1 0 0 20 10 10 0 0 0 0-20zm0 2c1 1.3 1.8 3.2 2 5h-4c.2-1.8 1-3.7 2-5zM4.3 11h3.7c.1 1.4.4 2.8.9 4H5a8 8 0 0 1-.7-4zm0-2A8 8 0 0 1 8 5.1 12 12 0 0 0 6.1 9zm5.7 2h4a11 11 0 0 1-1 4h-2a11 11 0 0 1-1-4zm6 0h3.7a8 8 0 0 1-.7 4h-3.9c.5-1.2.8-2.6.9-4zm-.1-2A12 12 0 0 0 16 5.1 8 8 0 0 1 19.7 9zM6 17h2.8c.5 1 1.1 1.9 1.7 2.7A8 8 0 0 1 6 17zm5.1 0h1.8l-.9 2zm4.1 0H18a8 8 0 0 1-4.5 2.7c.6-.8 1.2-1.7 1.7-2.7z"/></symbol>
  </defs>
</svg>

<section class="letterhead" aria-label="Letterhead">
  <header class="letterhead-header">
    <span class="brand">R&amp;W<span class="brand-dot"></span></span>
    <address class="letterhead-address" style="font-style:normal">PO Box 402, 55 Ochre St<br>Barrow Ridge NT 0870</address>
  </header>
  <footer class="letterhead-footer">
    <span class="footer-item"><svg class="icon"><use href="#i-phone"/></svg>08 5550 1987</span>
    <span class="footer-item"><svg class="icon"><use href="#i-mail"/></svg>office@rwgroup.com.au</span>
    <span class="footer-item"><svg class="icon"><use href="#i-globe"/></svg>www.rwgroup.com.au</span>
  </footer>
</section>

<section class="envelope-front" aria-label="Envelope front">
  <div class="envelope-return">
    <div class="envelope-row"><svg class="icon"><use href="#i-pin"/></svg><span>PO BOX 402, 55 OCHRE ST,<br>BARROW RIDGE NT 0870</span></div>
    <div class="envelope-row"><svg class="icon"><use href="#i-phone"/></svg><span>08 5550 1987</span></div>
  </div>
  <span class="brand">R&amp;W<span class="brand-dot"></span></span>
</section>

<section class="envelope-back" aria-label="Envelope back">
  <svg viewBox="0 0 540 270" width="540" height="270" aria-hidden="true">
    <path d="M0 60 L540 0 L250 175 Q225 190 195 186 L0 158 Z" fill="var(--flap-shadow)" transform="translate(0 10)"/>
    <path d="M0 50 L540 0 L250 165 Q225 180 195 176 L0 148 Z" fill="var(--navy)"/>
  </svg>
</section>

<section class="card card-front" aria-label="Business card front">
  <span class="brand">R&amp;W<span class="brand-dot"></span></span>
  <div class="card-name-band">
    <div class="card-name">DANA</div>
    <div class="card-title">Corporate Services Manager</div>
  </div>
  <div class="card-notch"></div>
  <div class="card-contact-band">
    <div class="card-contact-row"><svg class="icon"><use href="#i-pin"/></svg><span>PO Box 402, 55 Ochre St,<br>Barrow Ridge NT 0870</span></div>
    <div class="card-contact-row"><svg class="icon"><use href="#i-phone"/></svg><span>08 5550 1987</span></div>
    <div class="card-contact-row"><svg class="icon"><use href="#i-mobile"/></svg><span>0400 555 012</span></div>
    <div class="card-contact-row"><svg class="icon"><use href="#i-mail"/></svg><span>office@rwgroup.com.au</span></div>
  </div>
</section>

<section class="card card-back" aria-label="Business card back">
  <span class="brand">R&amp;W<span class="brand-dot"></span></span>
  <div class="card-back-strip"><svg class="icon"><use href="#i-globe"/></svg>www.rwgroup.com.au</div>
</section>

</body>
</html>
```